Toms welding and seed cleaning Business cards

Jakes welding and seed cleaningWe clean wheat seed on farm with portable cleaners so the farmers have pure wheat seed to plant back for the next crop. We are certified to clean foundation, registered, and certified seed wheat. Our cleaners being portable make it easier for the farmers because we do it right on there farm so they don't have to haul it all to townWhen there is no wheat to clean we weld in the winter. We improve, add onto, and build new corrals. We also build sheds, cattle shelters, and wind breaks. Other welding is welcomed

Reason: I need to extend the deadline because I've been busy and not had my game together. I need more time figure out what I want yet

Industry/Entity Type

Agriculture

Contact Information for Business Card

Just "toms welding and seed cleaning" on front and other info on the back
On the back side I would like to have my address.
Morris Tulane
48213 W COUNTY RD 318
HARLOW OK 73990
Phone #5804419362

Font styles to use
Sans Serif

Requirements
Must have
• list we are certified to clean foundation, registered, and certified wheat
• State that they are portable cleaners
• For the welding part list, add on to, improve on, and repair existing corrals and new corrals and other welding welcomed
Nice to have
• A wheat field with some metal corrals on the side with a nice classic looking barn for a background. Maybe some cattle in the corrals
• A nice looking farm yard would be good too

```html
<!DOCTYPE html>
<html lang="en">
<head>
<meta charset="utf-8">
<title>Toms welding and seed cleaning Business cards</title>
<link rel="stylesheet" href="https://fonts.googleapis.com/css2?family=Montserrat:wght@300;400;600;800&display=swap">
<style>
  :root {
    --bg: #5fcfbf;
    --green: #0bb162;
    --green-dark: #078a4c;
    --yellow: #dcd629;
    --white: #f2f2f0;
    --pill: #d9dcd9;
    --ink: #1d1d1b;
    --blue-text: #2a5d8c;
    --sky: #3d6fb0;
    --field: #c9a04a;
    --cloud-sky: #6a86b8;
  }
  * { box-sizing: border-box; margin: 0; padding: 0; }
  html, body { width: 1200px; height: 818px; overflow: hidden; }
  body {
    background: var(--bg);
    font-family: "Montserrat", sans-serif;
    position: relative;
  }
  .card {
    position: absolute;
    top: 266px;
    width: 500px;
    height: 286px;
    overflow: hidden;
    box-shadow: 0 6px 18px rgba(0,0,0,0.18);
  }
  /* Front */
  .card--front { left: 80px; background: var(--white); }
  .front-block { position: absolute; }
  .front-block--title {
    left: 0; top: 0; width: 250px; height: 143px;
    background: var(--green);
    display: flex; flex-direction: column; justify-content: flex-end;
    padding: 0 20px 18px;
    color: var(--ink);
  }
  .brand-name {
    font-weight: 300; font-size: 44px; letter-spacing: 1px; line-height: 1;
    text-transform: uppercase;
  }
  .brand-tagline {
    font-weight: 400; font-size: 11px; letter-spacing: 0.5px; margin-top: 4px;
  }
  .front-block--accent {
    right: 0; bottom: 0; width: 250px; height: 143px; background: var(--green);
  }
  .photo--field {
    right: 8px; top: 8px; width: 234px; height: 127px;
    background: linear-gradient(180deg, var(--cloud-sky) 0%, #d8d8d0 45%, var(--field) 70%, #a77f35 100%);
  }
  .photo--barn {
    left: 8px; bottom: 8px; width: 234px; height: 127px;
    background: linear-gradient(180deg, var(--sky) 0%, #8fb0d8 45%, var(--field) 60%, #b58a3c 100%);
  }
  /* Back */
  .card--back { left: 620px; background: var(--white); }
  .back-corner { position: absolute; right: 0; top: 0; }
  .back-contact {
    position: absolute; left: 0; top: 0; bottom: 0; width: 200px;
    background: var(--yellow);
    padding: 34px 22px;
    display: flex; flex-direction: column; gap: 16px;
  }
  .owner-name {
    font-weight: 800; font-size: 20px; text-transform: uppercase; color: var(--ink);
    letter-spacing: 0.5px; margin-bottom: 18px;
  }
  .owner-name span { font-weight: 300; }
  .contact-line {
    display: flex; align-items: flex-start; gap: 8px;
    font-size: 10px; color: var(--ink); line-height: 1.45;
  }
  .contact-line svg { flex: none; margin-top: 1px; }
  .back-services {
    position: absolute; left: 222px; top: 24px; right: 24px;
  }
  .service-title {
    display: inline-block; background: var(--pill);
    color: var(--blue-text); font-weight: 600; font-size: 10px;
    text-transform: uppercase; letter-spacing: 1px;
    padding: 4px 12px; border-radius: 10px; margin-bottom: 7px;
  }
  .service-list { list-style: none; margin-bottom: 14px; }
  .service-list li {
    font-size: 9.5px; color: var(--blue-text); line-height: 1.55;
    padding-left: 13px; position: relative;
  }
  .service-list li::before {
    content: ""; position: absolute; left: 2px; top: 5px;
    width: 4px; height: 4px; border-radius: 50%; background: var(--green);
  }
</style>
</head>
<body>

<section class="card card--front" aria-label="Card front">
  <div class="front-block front-block--title">
    <div class="brand-name">Toms</div>
    <div class="brand-tagline">welding and seed cleaning</div>
  </div>
  <div class="front-block front-block--accent"></div>
  <div class="front-block photo--field" role="img" aria-label="Photo of a wheat field under a cloudy sky with farm machinery"></div>
  <div class="front-block photo--barn" role="img" aria-label="Photo of a red barn beside a golden wheat field"></div>
</section>

<section class="card card--back" aria-label="Card back">
  <svg class="back-corner" width="160" height="90" viewBox="0 0 160 90" aria-hidden="true">
    <path d="M40 0 H160 V90 Q120 20 40 0 Z" fill="var(--yellow)"/>
  </svg>

  <div class="back-contact">
    <div class="owner-name">Morris <span>Tulane</span></div>
    <div class="contact-line">
      <svg width="12" height="12" viewBox="0 0 12 12" aria-hidden="true">
        <path d="M1 6 L6 1.5 L11 6 V11 H7.5 V8 H4.5 V11 H1 Z" fill="var(--green-dark)"/>
      </svg>
      <span>48213 W COUNTY RD 318<br>HARLOW OK 73990</span>
    </div>
    <div class="contact-line">
      <svg width="12" height="12" viewBox="0 0 12 12" aria-hidden="true">
        <path d="M3 1 L5 1 L6 4 L4.5 5 Q5.5 7 7 7.5 L8 6 L11 7 V9 Q10 11 8 11 Q2 10 1 4 Q1 2 3 1 Z" fill="var(--green-dark)"/>
      </svg>
      <span>5804419362</span>
    </div>
  </div>

  <div class="back-services">
    <div class="service-title">Welding</div>
    <ul class="service-list">
      <li>Add on to corrals</li>
      <li>Improve existing corrals</li>
      <li>Repair existing corrals</li>
      <li>Build new corrals</li>
      <li>Other welding welcomed</li>
    </ul>
    <div class="service-title">Seed Cleaning</div>
    <ul class="service-list">
      <li>Portable cleaners on your farm</li>
      <li>Certified to clean foundation, registered and certified wheat</li>
    </ul>
  </div>
</section>

</body>
</html>
```